Brightway Haus Inc. Business Card Design

Brightway Haus Inc. is in search of a great clean design for our business cards!

Looking to incorporate our full logo and watermark on side one (however, I am open to having the text and watermark separated within the design.)

On side two, I am looking to have contact information (Name, Position, Phone #, Email, Website (www.thebrightwayhaus.ca). Can have the logo and/or watermark as part of the design if applicable.

Please add tagline "Where Shine Counts" on either side 1 or 2. This tagline can be in a sans serif, serif or cursive font as long as it compliments overall design. Capitalization can be title or sentence case depending on how it fits within the design.

Get creative!! Looking for a clean, crisp, premium design! Looking for a glossy card finish with spot UV features when printed. Cards will also be printed with rounded corners. Standard dimensions (3.5 x 2).

Target Market(s)

B2B - primary clients are business owners or property management corporations. (residential jobs are few and far between)

Industry/Entity Type

Business

Contact Information for Business Card

- clean, crisp design
- double sided
- spot UV accents and glossy finish upon printing
- standard business card size (3.5 x 2) with rounded corners
- please see project description for requirements per side

Font styles to use
Sans Serif

Requirements
Must have
• - adequate bleeds with print ready files
• - cohesive design elements between side 1 & 2
• - spot UV elements (can be on both sides or just one, use your discretion)
• - colour pallet should match the logo file provided
• - incorporate tagline "where shine counts" (this tagline can be in a serif or sans serif font as long as it is complimentary to the overall design.
Nice to have
• - Premium elements with a clean design
Should not have
• - Please omit cartoon or whimsical like designs, think premium.
• - Colours should not stray from the pallet of the provided logo.

```html
<!DOCTYPE html>
<html lang="en">
<head>
<meta charset="utf-8">
<title>Brightway Haus Inc. Business Card</title>
<link rel="stylesheet" href="https://fonts.googleapis.com/css2?family=Open+Sans:wght@400;600;700;800&family=Roboto:ital,wght@0,400;1,400&display=swap">
<style>
  :root {
    --bg: #2a2a2a;
    --teal: #13aeb0;
    --navy: #1b2553;
    --paper: #f3f3f3;
    --ink: #4f4f4f;
    --white: #ffffff;
  }
  * { margin: 0; padding: 0; box-sizing: border-box; }
  html, body { width: 1200px; height: 960px; overflow: hidden; background: var(--bg); }
  body { position: relative; font-family: "Open Sans", Arial, sans-serif; }

  .card { position: absolute; width: 600px; height: 343px; border-radius: 18px; overflow: hidden; }
  .card--front { left: 314px; top: 113px; background: var(--paper); }
  .card--back { left: 311px; top: 472px; background: var(--teal); }

  .card__bands { position: absolute; inset: 0; }

  .wordmark { position: absolute; display: flex; align-items: center; gap: 12px; white-space: nowrap;
    font-weight: 800; font-size: 38px; letter-spacing: -0.5px; }
  .wordmark__square { width: 36px; height: 36px; }
  .card--front .wordmark { left: 0; right: 0; justify-content: center; top: 86px; color: var(--navy); }
  .card--front .wordmark__square { background: var(--teal); }
  .card--back .wordmark { left: 0; right: 0; justify-content: center; top: 144px; color: var(--white); }
  .card--back .wordmark__square { background: var(--white); }

  .identity { position: absolute; right: 320px; top: 186px; text-align: right; line-height: 19px; }
  .identity__name { font-size: 20px; font-weight: 600; color: var(--teal); line-height: 24px; }
  .identity__role { font-size: 14px; font-weight: 700; color: var(--navy); }
  .identity__line { font-size: 14px; color: var(--ink); }

  .divider { position: absolute; left: 300px; top: 182px; width: 1px; height: 86px; background: #9a9a9a; }

  .contacts { position: absolute; left: 322px; top: 189px; list-style: none; }
  .contacts li { display: flex; align-items: center; gap: 8px; height: 19px; font-size: 14px; color: var(--ink); }
  .contacts svg { width: 14px; height: 14px; fill: var(--teal); flex: none; }

  .tagline { position: absolute; left: 0; right: 0; top: 275px; display: flex; align-items: center; justify-content: center; gap: 6px; }
  .tagline__rule { width: 108px; height: 1px; background: rgba(255,255,255,0.8); }
  .tagline__text { font-family: "Roboto", Arial, sans-serif; font-style: italic; font-size: 18px; color: var(--white); }
</style>
</head>
<body>

<section class="card card--front" aria-label="Card front">
  <svg class="card__bands" viewBox="0 0 600 343" aria-hidden="true">
    <polygon points="0,0 69,0 4,343 0,343" fill="var(--teal)"/>
    <polygon points="600,0 600,343 531,343 598,0" fill="var(--navy)"/>
  </svg>

  <div class="wordmark"><span class="wordmark__square"></span>BRIGHTWAY HAUS INC.</div>

  <div class="identity">
    <div class="identity__name">MARA ELLISON</div>
    <div class="identity__role">CEO/FOUNDER</div>
    <div class="identity__line">2140 Alder Crescent</div>
    <div class="identity__line">Kelowna, Alaska 34810</div>
  </div>

  <div class="divider"></div>

  <ul class="contacts">
    <li><svg viewBox="0 0 24 24"><path d="M6.6 10.8a15 15 0 0 0 6.6 6.6l2.2-2.2a1 1 0 0 1 1-.25 11.4 11.4 0 0 0 3.6.57 1 1 0 0 1 1 1V20a1 1 0 0 1-1 1A17 17 0 0 1 3 4a1 1 0 0 1 1-1h3.5a1 1 0 0 1 1 1c0 1.25.2 2.45.57 3.57a1 1 0 0 1-.25 1z"/></svg>250 555 0142</li>
    <li><svg viewBox="0 0 24 24"><path d="M7 1h10a2 2 0 0 1 2 2v18a2 2 0 0 1-2 2H7a2 2 0 0 1-2-2V3a2 2 0 0 1 2-2zm0 3v14h10V4z"/></svg>250 555 0187</li>
    <li><svg viewBox="0 0 24 24"><path d="M6 2h12v5H6zM3 8h18a2 2 0 0 1 2 2v7h-4v5H5v-5H1v-7a2 2 0 0 1 2-2zm4 8v4h10v-4z"/></svg>250 555 0163</li>
    <li><svg viewBox="0 0 24 24"><path d="M2 5h20v14H2zm2 2v.5l8 5 8-5V7z"/></svg>mara@brightwayhaus.ca</li>
  </ul>
</section>

<section class="card card--back" aria-label="Card back">
  <div class="wordmark"><span class="wordmark__square"></span>BRIGHTWAY HAUS INC.</div>
  <div class="tagline">
    <span class="tagline__rule"></span>
    <span class="tagline__text">Where Shine Counts</span>
    <span class="tagline__rule"></span>
  </div>
</section>

</body>
</html>
```